Business Card Design

Hi I need a business card designed, we already have the business name logo artwork and would like some concept ideas for the Bus Card layout.
On the back of the card i want to include the products and services that we offer.
We are a Plastics Sheeting manufacture based in Perth Australia.

                                       

We need a BC design for a company called Tarvo Plastics based in Perth Australia.

We supply from DIY to Trade & Industrial  Engineering Markets.

We specialise in:

·         Cut to size panels  (all shapes and sizes)

·         Plastics fabrication & Welding

·         Custom Designs

·         Plastic Repairs

·         PVC Pipe Slotting & PVC Pipe Threading

·         Supplier of all types of engineering plastics and profiles.

Including:           Acrylic / Clarvene

                               Polycarbonate / Dorvil

                               Prismatic Light Diffuser

                               Vantrib

                               HDPE / UHMWPE

                               PVC / PVC Foam

                               Nylon

                               HIPS

```html
<!DOCTYPE html>
<html lang="en">
<head>
<meta charset="utf-8">
<title>Tarvo Plastics – Business Card</title>
<link rel="stylesheet" href="https://fonts.googleapis.com/css2?family=Open+Sans:ital,wght@0,400;0,600;0,700;0,800;1,700&display=swap">
<style>
  :root {
    --bg: #e6e7ea;
    --navy: #0f2a5e;
    --navy-deep: #0b2459;
    --orange: #e07a1f;
    --gold: #e3a614;
    --white: #ffffff;
    --ink: #2a2a2a;
  }
  * { box-sizing: border-box; margin: 0; padding: 0; }
  html, body { width: 1200px; height: 987px; overflow: hidden; }
  body {
    background: var(--bg);
    font-family: "Open Sans", sans-serif;
    display: flex; flex-direction: column; align-items: center; justify-content: center;
    gap: 40px;
  }
  .card {
    position: relative;
    width: 860px; height: 440px;
    border-radius: 34px;
    overflow: hidden;
    box-shadow: 0 6px 18px rgba(0,0,0,.12);
  }
  .wordmark {
    font-family: "Open Sans", sans-serif;
    font-weight: 800;
    color: var(--navy);
    letter-spacing: -1px;
    line-height: 1;
    display: flex; align-items: center; gap: 14px;
  }
  .wordmark__square { width: 22px; height: 22px; background: var(--navy); }

  /* Back */
  .card--back { background: var(--gold); text-align: center; }
  .card--back .wordmark { position: absolute; top: 30px; right: 60px; font-size: 56px; }
  .back__content { position: absolute; top: 110px; left: 0; right: 0; padding: 0 50px; }
  .back__intro { color: var(--white); font-weight: 700; font-style: italic; font-size: 21px; line-height: 1.3; }
  .back__heading { color: var(--navy); font-weight: 800; font-size: 24px; margin-top: 10px; }
  .back__list { color: var(--ink); font-size: 18.5px; line-height: 1.4; }

  /* Front */
  .card--front { background: var(--white); }
  .card--front .wordmark { position: absolute; top: 64px; left: 70px; font-size: 84px; }
  .front__band { position: absolute; inset: 0; }
  .front__name { position: absolute; top: 176px; right: 70px; font-size: 24px; font-weight: 700; color: var(--navy); }
  .front__title { color: var(--orange); font-weight: 400; }
  .contact { position: absolute; left: 40px; top: 272px; color: var(--white); font-size: 18.5px; line-height: 1.5; }
  .contact__icon { display: inline-block; vertical-align: -3px; width: 16px; height: 16px; margin-right: 4px; }
  .contact__sep { margin: 0 8px; }
</style>
</head>
<body>

<section class="card card--back">
  <div class="wordmark"><span class="wordmark__square"></span>Tarvo Plastics</div>
  <div class="back__content">
    <p class="back__intro">The Products And Services That We Offer<br>Are Supplied From Diy To Trade &amp; Industrial Engineering Markets</p>
    <p class="back__heading">We specialise in:</p>
    <p class="back__list">• Cut to size panels (all shapes and sizes) • Plastics fabrication &amp; Welding<br>
      • Custom Designs • Plastic Repairs • PVC Pipe Slotting &amp; PVC Pipe Threading<br>
      • Supplier of all types of engineering plastics and profiles</p>
    <p class="back__heading">Including:</p>
    <p class="back__list">• Acrylic / Clarvene • Polycarbonate / Dorvil • Prismatic Light Diffuser • Vantrib<br>
      • HDPE / UHMWPE • PVC / PVC Foam • Nylon • HIPS</p>
  </div>
</section>

<section class="card card--front">
  <svg class="front__band" viewBox="0 0 860 440" width="860" height="440" aria-hidden="true">
    <path d="M0,202 Q600,196 860,430" fill="none" stroke="var(--orange)" stroke-width="4"/>
    <path d="M0,214 Q600,210 860,440 L0,440 Z" fill="var(--navy-deep)"/>
  </svg>
  <div class="wordmark"><span class="wordmark__square"></span>Tarvo Plastics</div>
  <p class="front__name">Your Name, <span class="front__title">Title</span></p>
  <div class="contact">
    <p>Unit 4/18 Brenlow Circuit Canning Vale WA 6155</p>
    <p>PO Box 2284 Canning Vale DC WA 6970</p>
    <p>
      <svg class="contact__icon" viewBox="0 0 16 16"><path d="M4 1l3 3-2 2c1 2 3 4 5 5l2-2 3 3-2 3C7 15 1 9 1 3z" fill="currentColor"/></svg>08 9000 4121
      <svg class="contact__icon" viewBox="0 0 16 16"><rect x="4" y="1" width="8" height="14" rx="1.5" fill="none" stroke="currentColor" stroke-width="1.6"/><rect x="7" y="12" width="2" height="1.5" fill="currentColor"/></svg>123-456-7890
      <svg class="contact__icon" viewBox="0 0 16 16"><rect x="2" y="6" width="12" height="8" rx="1" fill="currentColor"/><rect x="4" y="2" width="8" height="4" fill="none" stroke="currentColor" stroke-width="1.4"/></svg>08 9000 4122
    </p>
    <p>
      <svg class="contact__icon" viewBox="0 0 16 16"><rect x="1" y="3" width="14" height="10" rx="1" fill="none" stroke="currentColor" stroke-width="1.6"/><path d="M1 4l7 5 7-5" fill="none" stroke="currentColor" stroke-width="1.6"/></svg>sales@tarvoplastics.com.au<span class="contact__sep">|</span>Keldon Holdings Pty Ltd T/A Tarvo Plastics ABN: TBA
    </p>
  </div>
</section>

</body>
</html>
```